Round Label Sticker 2.5-3 inch diameter

We need a design for a sticker to distribute for more brand recognition and product outreach.
My company The Brisk Lark Company Ltd. Specializes in working with people with diabetes. My products are made for diabetics because they have no added sugars, high in protein and fiber and each serving is lower than 5% daily value of carbohydrates.
I am a dietitian and my dad passed away from diabetes. I have created a growing food and beverage line that will give more joy into a diabetic's life while providing more food options that make them feel happy instead of guilty when they eat it.
I am teaching cooking classes to promote my products as well as doing exhibits and events. I want to give away a sticker to people that reads "I'm too sweet for sugar!" and somewhere on it would be my logo as well as my website info. www.brisklark-example.com
The sticker should make people smile and warm as well as draw interest to my product line.
Target Market(s)
Diabetes and people who do not want added sugars in their food
Industry/Entity Type
Food Store
Requirements
Must have
- my logo and website

```html
<!DOCTYPE html>
<html lang="en">
<head>
<meta charset="utf-8">
<title>Brisk Lark – I'm too Sweet for sugar! Sticker</title>
<link rel="stylesheet" href="https://fonts.googleapis.com/css2?family=Chewy&family=Lobster&family=Montserrat:wght@500&display=swap">
<style>
  :root {
    --page-bg: #ffffff;
    --sticker-edge: #8a8a8a;
    --sticker-center: #fff6f6;
    --sticker-mid: #fde6e7;
    --sticker-rim: #f6c4c8;
    --brand-purple: #5b2a86;
    --rule-pink: #e07b7b;
    --url-pink: #d65a66;
    --slogan-green: #8cc63f;
    --slogan-shadow: #2f6b1d;
    --slogan-outline: #ffffff;
    --placeholder-top: #e9d3dc;
    --placeholder-bottom: #f1d6c8;
  }
  * { margin: 0; padding: 0; box-sizing: border-box; }
  html, body {
    width: 1200px; height: 1200px; overflow: hidden;
    background: var(--page-bg);
  }
  .canvas { position: relative; width: 1200px; height: 1200px; }

  .sticker {
    position: absolute; left: 100px; top: 100px;
    width: 1000px; height: 1000px; border-radius: 50%;
    border: 2px solid var(--sticker-edge);
    background: radial-gradient(circle at 50% 48%, var(--sticker-center) 0%, var(--sticker-mid) 45%, var(--sticker-rim) 100%);
    overflow: hidden;
  }

  .illustration-slot {
    position: absolute; left: 155px; top: 355px;
    width: 375px; height: 345px; border-radius: 24px;
    background: linear-gradient(160deg, var(--placeholder-top), var(--placeholder-bottom));
  }

  .brand {
    position: absolute; left: 587px; top: 300px; width: 326px;
    text-align: center;
  }
  .brand-name {
    font-family: "Chewy", "Arial Rounded MT Bold", sans-serif;
    font-size: 88px; line-height: 1; white-space: nowrap;
    color: var(--brand-purple);
  }
  .brand-url {
    margin-top: 28px;
    border-top: 3px solid var(--rule-pink);
    border-bottom: 3px solid var(--rule-pink);
    padding: 9px 0 10px;
    font-family: "Montserrat", Arial, sans-serif; font-weight: 500;
    font-size: 21px; white-space: nowrap;
    color: var(--url-pink);
  }

  .slogan {
    position: absolute; left: 0; top: 0; width: 1200px; height: 1200px;
    overflow: visible;
  }
  .slogan text {
    fill: var(--slogan-green);
    stroke: var(--slogan-outline); stroke-width: 12px; stroke-linejoin: round;
    paint-order: stroke fill;
    filter: drop-shadow(4px 6px 0 var(--slogan-shadow));
  }
  .slogan-lead, .slogan-tail { font-family: "Chewy", "Arial Rounded MT Bold", sans-serif; }
  .slogan-lead { font-size: 120px; }
  .slogan-tail { font-size: 110px; }
  .slogan-key { font-family: "Lobster", "Brush Script MT", cursive; font-size: 250px; }
</style>
</head>
<body>
<main class="canvas">
  <div class="sticker">
    <div class="illustration-slot" role="img" aria-label="Illustration area: cheerful cartoon glazed doughnut with sprinkles"></div>
  </div>

  <div class="brand">
    <div class="brand-name">Brisk Lark</div>
    <div class="brand-url">www.brisklark-example.com</div>
  </div>

  <svg class="slogan" viewBox="0 0 1200 1200" role="heading" aria-level="1" aria-label="I'm too Sweet for sugar!">
    <g transform="rotate(-10 600 760)">
      <text class="slogan-lead" x="205" y="775" textLength="345" lengthAdjust="spacingAndGlyphs">I'm too</text>
      <text class="slogan-key" x="565" y="800" textLength="465" lengthAdjust="spacingAndGlyphs">Sweet</text>
      <text class="slogan-tail" x="420" y="915" textLength="440" lengthAdjust="spacingAndGlyphs">for sugar!</text>
    </g>
  </svg>
</main>
</body>
</html>
```